Puffy Clouds Cotton Candy

Looking for a logo design and business cards to help a 13 year old entrepreneur promote her cotton candy business.
Contact Information for Business Card
Name, Phone & Email
Colors
E54698
E96AAD
F1A4CE
F9D9EA
FCEFF6
A7469A
B969AE
D3A5CF
EDDBEB
F8F0F9
6B429C
8869AF
B7A5CE
E3DAEB
F3F0F8
Requirements
Must have
- A fun feel that is appropriate for a teenage girl selling cotton candy

```html
<!DOCTYPE html>
<html lang="en">
<head>
<meta charset="utf-8">
<title>Puffy Clouds Cotton Candy – Business Cards</title>
<link rel="stylesheet" href="https://fonts.googleapis.com/css2?family=Quicksand:wght@400;500&display=swap">
<style>
  :root {
    --bg: #fce6f1;
    --pink: #f47eb5;
    --pink-deep: #e96aad;
    --white: #ffffff;
    --ink: #2b2b2b;
    --shadow: rgba(180, 80, 130, 0.18);
  }
  * { box-sizing: border-box; margin: 0; padding: 0; }
  html, body { width: 1200px; height: 1200px; overflow: hidden; }
  body {
    background: var(--bg);
    font-family: "Quicksand", sans-serif;
    position: relative;
  }
  .card {
    position: absolute;
    top: 240px;
    width: 400px;
    height: 700px;
    box-shadow: 0 24px 48px var(--shadow);
    overflow: hidden;
  }
  .card--front { left: 160px; background: var(--pink); }
  .card--back { left: 640px; background: var(--white); }

  .brand {
    position: absolute;
    left: 50%;
    transform: translateX(-50%);
    width: 290px;
    height: 290px;
    border-radius: 50%;
    border: 4px solid currentColor;
    display: flex;
    flex-direction: column;
    align-items: center;
    justify-content: center;
    text-align: center;
    font-weight: 500;
  }
  .card--front .brand { top: 150px; color: var(--white); }
  .card--back .brand { top: 110px; color: var(--pink-deep); }
  .brand__name { font-size: 40px; line-height: 1.1; }
  .brand__sub {
    font-size: 17px;
    letter-spacing: 4px;
    text-transform: uppercase;
    margin-top: 14px;
  }

  .tagline {
    position: absolute;
    top: 500px;
    width: 100%;
    text-align: center;
    color: var(--white);
    font-size: 19px;
    letter-spacing: 6px;
    line-height: 1.9;
    text-transform: uppercase;
  }

  .contact-band {
    position: absolute;
    left: 0;
    bottom: 0;
    width: 400px;
    height: 270px;
  }
  .contact {
    position: absolute;
    left: 0;
    bottom: 0;
    width: 100%;
    height: 240px;
    display: flex;
    flex-direction: column;
    align-items: center;
    padding-top: 60px;
    color: var(--white);
  }
  .contact__icon { width: 40px; height: 40px; }
  .contact__phone {
    margin-top: 26px;
    font-size: 30px;
    letter-spacing: 8px;
  }
</style>
</head>
<body>

  <section class="card card--front" aria-label="Card front">
    <div class="brand">
      <span class="brand__name">Puffy Clouds</span>
      <span class="brand__sub">Cotton Candy</span>
    </div>
    <p class="tagline">Share moments,<br>share puffy clouds</p>
  </section>

  <section class="card card--back" aria-label="Card back">
    <div class="brand">
      <span class="brand__name">Puffy Clouds</span>
      <span class="brand__sub">Cotton Candy</span>
    </div>

    <svg class="contact-band" viewBox="0 0 400 270" aria-hidden="true">
      <path fill="#f47eb5"
        d="M0 30 q10 -14 20 0 t20 0 t20 0 t20 0 t20 0 t20 0 t20 0 t20 0 t20 0 t20 0 t20 0 t20 0 t20 0 t20 0 t20 0 t20 0 t20 0 t20 0 t20 0 t20 0 V270 H0 Z"/>
    </svg>

    <div class="contact">
      <svg class="contact__icon" viewBox="0 0 40 40" aria-label="Phone">
        <circle cx="20" cy="20" r="20" fill="#ffffff"/>
        <rect x="14" y="9" width="12" height="22" rx="2" fill="none" stroke="#f47eb5" stroke-width="2"/>
        <line x1="17" y1="12" x2="23" y2="12" stroke="#f47eb5" stroke-width="1.5"/>
        <circle cx="20" cy="27.5" r="1.3" fill="#f47eb5"/>
      </svg>
      <span class="contact__phone">555.014.2378</span>
    </div>
  </section>

</body>
</html>
```